Kelvaro.ch is looking for business card letterhead and envelope C5 with WOW effect

We need a strong business card for our company Kelvaro.ch, logo is available. You want a black or dark background on which the logo Stark r% 26 # 252; appears. Letterhead and envelope in C5 format should be in a similar design, but does not have to be We need a strong business card for our company Kelvaro.ch, logo is available. A black or dark background is desired, on which the logo Stark comes across. The letterhead and the envelope in C5 format should have a similar design.

Target Market(s)

Private customers as well as entrepreneurs

Contact Information for Business Card

E-mail: info@kelvaro-example.ch
Web.www.Kelvaro-example.ch
Tel: +41 ( 0 ) 79 482 6037
Adresse:
Lindenweg 14
9406 Tarnbach

Hier kann man Icons verwenden für Email,Tel und Adressse

Font styles to use
Other font styles liked:
• Dubai,bold

Colors

Designer to choose colors to be used in the design.

Requirements
Must have
• WOW effect
Nice to have
• R% 26 # 252; back business card with our service listings. - VEHICLE LABELING - SHOP WINDOW LABELING - STICKERS AND MUCH MORE ... in red color

```html
<!DOCTYPE html>
<html lang="en">
<head>
<meta charset="utf-8">
<title>Kelvaro.ch – Business Card</title>
<link rel="stylesheet" href="https://fonts.googleapis.com/css2?family=Lato:wght@400;700;900&display=swap">
<style>
  :root {
    --backdrop: #dedede;
    --card-white: #ffffff;
    --card-black: #070707;
    --honey: #fdcb1f;
    --honey-faint: #fdf3dc;
    --ink: #111111;
    --grey-text: #8a8a8a;
    --white: #ffffff;
  }
  * { margin: 0; padding: 0; box-sizing: border-box; }
  html, body {
    width: 1200px; height: 960px; overflow: hidden;
    background: var(--backdrop);
    font-family: "Lato", Arial, sans-serif;
  }
  .canvas { position: relative; width: 1200px; height: 960px; }
  .card {
    position: absolute; left: 281px; width: 655px; height: 374px;
    border-radius: 26px; overflow: hidden;
  }
  .card--front { top: 81px; background: var(--card-white); }
  .card--back { top: 506px; background: var(--card-black); }

  .front-texture {
    position: absolute; left: 0; top: 90px; width: 165px; height: 284px;
    background: linear-gradient(160deg, rgba(253,243,220,0) 0%, var(--honey-faint) 55%, rgba(253,243,220,0.6) 100%);
  }
  .brand {
    position: absolute; left: 92px; top: 94px;
    display: flex; align-items: center; gap: 14px;
  }
  .brand__dot { width: 22px; height: 22px; border-radius: 50%; background: var(--honey); }
  .brand__name {
    font-weight: 900; font-size: 25px; color: var(--ink); letter-spacing: 0.5px;
    text-transform: uppercase;
  }

  .person { position: absolute; left: 365px; top: 84px; }
  .person__name { font-weight: 700; font-size: 28px; color: var(--honey); line-height: 34px; }
  .person__role { font-size: 18px; color: var(--grey-text); line-height: 26px; margin-top: 0; }

  .address {
    position: absolute; left: 365px; top: 178px;
    font-size: 18px; line-height: 23px; color: var(--grey-text); font-style: normal;
  }
  .contacts { position: absolute; left: 365px; top: 241px; list-style: none; }
  .contacts__item {
    display: flex; align-items: center; gap: 8px;
    font-size: 18px; line-height: 24px; color: var(--grey-text);
  }
  .contacts__icon { width: 12px; height: 12px; flex: none; }

  .back-texture { position: absolute; left: 0; top: 0; width: 655px; height: 374px; }
  .back-brand {
    position: absolute; left: 406px; top: 126px; transform: translateX(-50%);
    text-align: center; color: var(--white);
  }
  .back-brand__name {
    font-weight: 900; font-size: 37px; line-height: 42px; letter-spacing: 1px;
    text-transform: uppercase;
  }
  .back-brand__url { font-size: 17px; line-height: 24px; margin-top: 2px; }
</style>
</head>
<body>
<main class="canvas">
  <section class="card card--front">
    <div class="front-texture" role="img" aria-label="Faint honeycomb pattern in pale yellow"></div>
    <div class="brand">
      <span class="brand__dot"></span>
      <span class="brand__name">Kelvaro.ch</span>
    </div>
    <div class="person">
      <p class="person__name">Marco Lindqvist</p>
      <p class="person__role">Managing Director</p>
    </div>
    <address class="address">Lindenweg 14<br>9406 Tarnbach</address>
    <ul class="contacts">
      <li class="contacts__item">
        <svg class="contacts__icon" viewBox="0 0 12 12"><path d="M2 1 L4.5 1 L5 3.5 L3.6 4.5 C4.3 6 5.8 7.6 7.4 8.3 L8.5 7 L11 7.5 L11 10 C6 10.5 1.5 6 2 1 Z" fill="var(--honey)"/></svg>
        +41 ( 0 ) 79 482 6037
      </li>
      <li class="contacts__item">
        <svg class="contacts__icon" viewBox="0 0 12 12"><rect x="0.5" y="2.5" width="11" height="7" fill="var(--honey)"/><path d="M0.8 2.8 L6 6.6 L11.2 2.8" fill="none" stroke="#fff" stroke-width="1"/></svg>
        info@kelvaro-example.ch
      </li>
      <li class="contacts__item">
        <svg class="contacts__icon" viewBox="0 0 12 12"><g fill="none" stroke="var(--honey)" stroke-width="1"><circle cx="6" cy="6" r="5"/><ellipse cx="6" cy="6" rx="2.2" ry="5"/><path d="M1 6 H11 M2 3.3 H10 M2 8.7 H10"/></g></svg>
        www.kelvaro-example.ch
      </li>
    </ul>
  </section>

  <section class="card card--back">
    <svg class="back-texture" viewBox="0 0 655 374" role="img" aria-label="Yellow honeycomb pattern along the left and bottom edge">
      <defs>
        <linearGradient id="honeyFade" x1="0" y1="0" x2="1" y2="1">
          <stop offset="0" stop-color="#fdcb1f"/>
          <stop offset="1" stop-color="#e6b512"/>
        </linearGradient>
      </defs>
      <polygon points="0,0 145,0 195,70 150,160 200,260 270,250 350,330 320,374 0,374" fill="url(#honeyFade)"/>
    </svg>
    <div class="back-brand">
      <p class="back-brand__name">Kelvaro.ch</p>
      <p class="back-brand__url">www.kelvaro-example.ch</p>
    </div>
  </section>
</main>
</body>
</html>
```